Two flyers with cover pages for business services company

We need to create two double sided A4 flyers for our company. We are a company that provides professional services for businesses in Dubai, UAE.
Please note that there are two different flyers. The design must be identical. Each has a cover page. The cover page will be duplicated for both flyers.
Please note that we have added images of the Dubai skyline, clip art as place-hold/temporary images. These can be changed to be more fitting to your design. We prefer to have free images where possible but are open to purchasing Framevault images if required.
We have recommended a colour palet below. You are welcome to change some colours to be more fitting to the design. However, we must have black, white and blue and per the logo.
Target Market(s)
Businesses, entrepreneurs, professionals
Industry/Entity Type
Business Service
Requirements
Must have
- The cover page should be less crowded and more visual. So mostly images with our logo and tagline.

```html
<!DOCTYPE html>
<html lang="en">
<head>
<meta charset="utf-8">
<title>Nexora – Business Services Flyer</title>
<link href="https://fonts.googleapis.com/css2?family=Raleway:wght@400;700&family=Roboto+Condensed:wght@300;400;700&display=swap" rel="stylesheet">
<style>
  :root{
    --backdrop:#e3e3e3;
    --paper:#ffffff;
    --sky-blue:#1b8ac4;
    --royal-blue:#1d4fa3;
    --badge-blue:#2f6fb6;
    --orange:#ec8a22;
    --ink:#222222;
    --warm-tone:#f3e2d7;
    --cool-tone:#dcdde2;
  }
  *{box-sizing:border-box;margin:0;padding:0}
  html,body{width:1200px;height:1200px;overflow:hidden;background:var(--backdrop)}
  .page{position:absolute;top:194px;width:555px;height:786px;background:var(--paper);overflow:hidden;box-shadow:0 4px 10px rgba(0,0,0,.18)}
  .cover{left:35px}
  .inside{left:611px;font-family:"Roboto Condensed",sans-serif;color:var(--ink)}

  /* cover */
  .cover-photo{position:absolute;inset:0;background:linear-gradient(165deg,var(--paper) 0%,var(--paper) 35%,var(--warm-tone) 65%,var(--cool-tone) 100%)}
  .cover-title{position:absolute;left:276px;top:40px;font-family:"Raleway",sans-serif;font-weight:700;font-size:34px;line-height:43px;color:var(--sky-blue);letter-spacing:-.6px;white-space:nowrap}
  .brand{position:absolute;left:24px;top:696px;display:flex;align-items:center;gap:10px}
  .brand-dot{width:42px;height:42px;border-radius:50%;background:var(--sky-blue)}
  .brand-name{font-family:"Raleway",sans-serif;font-weight:400;font-size:40px;color:var(--ink)}
  .cover-web{position:absolute;left:374px;top:728px;font-family:"Raleway",sans-serif;font-size:21px;letter-spacing:1px;color:var(--sky-blue)}

  /* inside */
  .inside-title{position:absolute;left:0;right:0;top:14px;text-align:center;font-weight:300;font-size:35px;line-height:38px;color:var(--royal-blue)}
  .team-photo{position:absolute;left:0;top:99px;width:555px;height:257px;background:linear-gradient(90deg,#f2f3f5 0%,#c9ccd2 45%,#6a6e76 75%,#e4e6e9 100%)}
  .badge{position:absolute;width:140px;height:140px;border-radius:50%;background:var(--badge-blue);border:5px solid var(--orange);color:#fff;display:flex;flex-direction:column;justify-content:center;align-items:center;text-align:center;font-size:17px;line-height:16px;font-weight:300}
  .badge b{font-weight:700}
  .badge-price{left:31px;top:336px}
  .badge-guarantee{left:31px;top:492px}
  .offer{position:absolute;left:182px;width:360px}
  .offer h2{font-weight:400;font-size:16px;color:var(--sky-blue);margin-bottom:6px}
  .offer p{font-weight:300;font-size:13.5px;line-height:20px}
  .offer-network{top:373px}
  .offer-best{top:449px}
  .offer ul{list-style:none;font-weight:300;font-size:12.8px;line-height:18.5px}
  .offer li::before{content:"- "}
  .offer b{font-weight:700}
  .call{position:absolute;left:21px;top:670px;font-size:14px;font-weight:300}
  .call b{font-weight:700}
  .phone{position:absolute;left:20px;top:688px;font-size:33px;font-weight:400;color:var(--orange)}
  .contact{position:absolute;top:733px;display:flex;align-items:center;gap:6px;font-size:11.5px;line-height:13px;font-weight:300}
  .contact-address{left:22px}
  .contact-web{left:190px}
  .portrait{position:absolute;left:319px;top:656px;width:116px;height:116px;border-radius:50%;border:3px solid var(--orange);background:linear-gradient(180deg,#e3e6ea,#8a93a0)}
  .director{position:absolute;left:430px;top:682px;width:103px;height:62px;background:var(--orange);color:#fff;padding:12px 6px 0 10px;font-size:15px;line-height:17px}
  .director i{font-size:12px}
</style>
</head>
<body>

<section class="page cover">
  <div class="cover-photo" role="img" aria-label="Photo: close-up handshake between two business partners"></div>
  <h1 class="cover-title">Are you getting<br>REAL value<br>from your<br>current sponsor?</h1>
  <div class="brand"><span class="brand-dot"></span><span class="brand-name">Nexora</span></div>
  <div class="cover-web">www.nexora.ae</div>
</section>

<section class="page inside">
  <h1 class="inside-title">DO YOU NEED HELP TO INCREASE<br>YOUR SALES?</h1>
  <div class="team-photo" role="img" aria-label="Photo: three businessmen reviewing documents at an office desk"></div>

  <div class="badge badge-price">AS LOW AS<br><span><b>1,500 AED</b> EASY</span>MONTHLY<br>INSTALLMENTS</div>
  <div class="badge badge-guarantee"><b>SATISFACTION<br>GUARANTEED</b>100%<br>OR YOUR<br>MONEY BACK</div>

  <div class="offer offer-network">
    <h2>Grow Your Business Through Our Extensive Network</h2>
    <p>Use our <b>3,000+ Business Connections,</b><br><b>570+Decision Makers,</b> MDs, CEOs, Heads of Purchasing</p>
  </div>
  <div class="offer offer-best">
    <h2>The Best Offer in the Market</h2>
    <ul>
      <li><b>50% off</b> your current sponsorship fees</li>
      <li><b>Free sponsorship</b> for 12 months</li>
      <li>Low monthly installments (starting at &nbsp;AED 1,500)</li>
      <li>We can be active or silent sponsors</li>
      <li>Unique legal structure which allows you to exit any time</li>
      <li>Help you increase your sales</li>
      <li>VIP introductions and connections</li>
      <li>Legal and mediation support</li>
      <li>We have been in this market since 2004</li>
    </ul>
  </div>

  <div class="call">CALL US NOW FOR A <b>FREE CONSULTATION</b> ON</div>
  <div class="phone">04 555 0192</div>
  <div class="contact contact-address">
    <svg width="16" height="24" viewBox="0 0 16 24"><path d="M8 1a7 7 0 0 0-7 7c0 5 7 15 7 15s7-10 7-15a7 7 0 0 0-7-7z" fill="none" stroke="#222" stroke-width="2"/><circle cx="8" cy="8" r="2.5" fill="#222"/></svg>
    <span>Corniche Business Tower,<br>24th Floor Dubai, UAE</span>
  </div>
  <div class="contact contact-web">
    <svg width="22" height="22" viewBox="0 0 22 22" fill="none" stroke="#222" stroke-width="1.4"><circle cx="11" cy="11" r="10"/><ellipse cx="11" cy="11" rx="4.5" ry="10"/><path d="M1 11h20M3 5.5h16M3 16.5h16"/></svg>
    <span>www.nexora.ae</span>
  </div>
  <div class="portrait" role="img" aria-label="Photo: portrait of the managing director"></div>
  <div class="director">Daniel Hart,<br><i>Managing Director</i></div>
</section>

</body>
</html>
```